African homeware retailer needs a web page design

We need a web page design for a new homeware and accessories store based in Johannesburg, South Africa. Our store carries modern African inspired items from designers that support social development and poverty alleviation initiatives. We have a particular preference for outfits that are centred on the empowerment of women.

Our business celebrates the skill, design and product of African craft and the work of designers looking to take that forward in a socially beneficial way (creating employment, developing skills, supporting local crafts people etc). We aim to carry items and inspirations from all over the African continent.

We would like to see a design that communicates African beauty and elegance without the typical tribal references that are made in reference to African craft or art.

We would like the web page to be stylish, uncomplicated, modern, captivating and appealing to the discerning customer. A similar value proposition is that of http://www.marlowtenwick.example/.

This is an e-commerce website which must be attractive to both individual buyers and design professionals so the website needs to look professional.

Here are links to some websites we like:
http://www.quenbyhollis.example/
http://www.dravelo.example/

Our logo is attached to the brief.

Target Market(s)

Our target market is female, age 20-50. However should not alienate the design conscious male customer therefore

Industry/Entity Type

E-Commerce

Requirements
Must have
• - A featured product banner which includes a photograph and text. This should be easy to edit as we will be changing the featured product regularly
- An easily expendable products section with categories. Examples of categories could be cushions, bedding, crockery etc. Should be easy to add new categories as well as new product pictures
- Home/landing page should be uncluttered
- Should use the logo and should be easy to change the logo which we have in various colour combinations. We plan to change the logo colours depending on circumstance e.g. make it red and white around Valentines day (similar to the way Vintrel frequently changes the logo on their landing page)

```html
<!DOCTYPE html>
<html lang="en">
<head>
<meta charset="utf-8">
<title>Amani Living — Homeware &amp; Accessories</title>
<link href="https://fonts.googleapis.com/css2?family=Open+Sans:wght@400;600;700&family=Ubuntu:wght@400;500;700&family=Noto+Sans:wght@400;700&display=swap" rel="stylesheet">
<style>
:root{
  --navy:#0e3d5c;
  --green:#3a963d;
  --green-dark:#2f8434;
  --cream:#fcf5d8;
  --tan:#a28a6b;
  --grey-line:#d9d9d9;
  --text:#555;
  --white:#fff;
}
*{box-sizing:border-box;margin:0;padding:0}
html,body{width:1200px;height:2195px;overflow:hidden}
body{position:relative;background:var(--white);font-family:"Open Sans",Arial,sans-serif;color:var(--text)}
.abs{position:absolute}

/* top utility bar */
.utility-bar{left:0;top:0;width:1200px;height:22px;background:var(--navy)}
.utility-links{position:absolute;right:186px;top:3px;font-size:11px;font-weight:600;color:var(--white);display:flex;gap:10px;white-space:nowrap}

/* header */
.site-header{left:0;top:22px;width:1200px;height:155px;background:var(--cream)}
.brand-name{position:absolute;left:195px;top:44px;font-family:"Ubuntu",sans-serif;font-weight:700;font-size:54px;letter-spacing:2px;color:var(--green);line-height:1;white-space:nowrap}
.phone{position:absolute;left:822px;top:58px;display:flex;align-items:center;gap:8px;font-family:"Open Sans",sans-serif;font-weight:700;font-size:21px;color:var(--green);letter-spacing:.5px;white-space:nowrap}
.search{position:absolute;left:792px;top:125px;width:222px;height:20px;background:var(--white);border:1px solid #cfcfcf;font-size:11px;color:#444;padding:2px 5px}
.search svg{position:absolute;right:5px;top:3px}

/* navigation */
.main-nav{left:0;top:177px;width:1200px;height:34px;background:var(--navy)}
.nav-item{position:absolute;top:9px;font-size:13.5px;color:var(--white);white-space:nowrap}
.nav-item.active{top:2px;left:189px;width:83px;height:32px;background:var(--green);font-weight:700;text-align:center;line-height:32px}

/* hero */
.hero{left:0;top:211px;width:1200px;height:524px;background:linear-gradient(90deg,#fff 0%,#f6f6f6 40%,#e4e4e4 100%);border-bottom:3px solid #cfcfcf;box-shadow:inset 0 8px 10px -6px rgba(0,0,0,.25)}
.hero-title{position:absolute;left:187px;top:90px;font-family:"Noto Sans",sans-serif;font-weight:700;font-size:37px;line-height:50px;color:var(--navy)}
.hero-copy{position:absolute;left:188px;top:205px;width:290px;font-family:"Noto Sans",sans-serif;font-size:20px;line-height:26px;color:var(--navy)}
.buy-button{position:absolute;left:181px;top:428px;width:264px;height:42px;background:var(--green);border-radius:4px;color:var(--white);font-family:"Noto Sans",sans-serif;font-weight:700;font-size:25px;letter-spacing:1px;padding-left:48px;line-height:42px;white-space:nowrap}
.buy-button .go{position:absolute;right:22px;top:8px}
.hero-feature{position:absolute;left:509px;top:13px}
.hero-price{position:absolute;left:712px;top:385px;font-family:"Open Sans",sans-serif;font-weight:600;font-size:25px;color:var(--white);white-space:nowrap}

/* promo cards */
.promo{top:758px;width:268px;height:347px}
.promo-image{position:absolute;left:0;top:0;width:268px;height:237px;border:1px solid #cfcfcf}
.promo-text{position:absolute;left:0;top:237px;width:268px;height:72px;border:1px solid #cfcfcf;border-top:none;text-align:center;padding-top:10px}
.promo-text strong{display:block;font-family:"Ubuntu",sans-serif;font-weight:700;font-size:19px;color:var(--green);letter-spacing:.3px;white-space:nowrap}
.promo-text span{display:block;font-family:"Ubuntu",sans-serif;font-size:19px;color:#666;letter-spacing:.3px;white-space:nowrap}
.promo-button{position:absolute;left:0;top:315px;width:268px;height:32px;background:var(--green);color:var(--white);font-size:12.5px;text-align:center;line-height:32px;white-space:nowrap}
.promo-button svg{vertical-align:middle;margin-left:6px;margin-top:-2px}

.soft-divider{left:210px;width:780px;height:8px;border-radius:50%;box-shadow:0 5px 6px -3px rgba(0,0,0,.18)}

/* section headings */
.section-title{left:186px;width:828px;text-align:center;font-family:"Ubuntu",sans-serif;font-weight:700;font-size:28px;color:var(--green)}
.rule{left:186px;width:828px;height:2px;background:#e3e3e3}
.arrow{position:absolute}

/* featured products */
.product{top:1228px;width:195px;text-align:center}
.product-image{width:195px;height:193px;border:1px solid #ddd}
.product-name{margin-top:20px;font-weight:700;font-size:15px;color:var(--navy);letter-spacing:.3px}
.product-desc{font-size:12.5px;line-height:18px;color:#666;white-space:nowrap}

/* categories */
.category{width:164px;height:33px;border:1px solid #d4d4d4;background:linear-gradient(#fff,#f1f1f1);font-family:"Ubuntu",sans-serif;font-size:19px;color:var(--green);text-align:center;line-height:31px;white-space:nowrap}

/* newsletter strip */
.newsletter-strip{left:186px;top:1810px;width:828px;height:56px;border-top:2px solid #e3e3e3;border-bottom:2px solid #e3e3e3}
.strip-label{position:absolute;top:14px;font-family:"Open Sans",sans-serif;font-weight:700;font-size:19px;color:var(--green);white-space:nowrap}
.email-field{position:absolute;left:139px;top:15px;width:167px;height:26px;border:1px solid #ccc;font-size:12px;color:#aaa;padding:4px 7px;white-space:nowrap}
.email-submit{position:absolute;left:316px;top:15px;width:79px;height:26px;background:var(--tan);color:var(--white);font-size:15px;text-align:center;line-height:26px}
.strip-divider{position:absolute;left:421px;top:6px;width:1px;height:42px;background:#d6d6d6}
.pay-method{position:absolute;top:12px;height:32px;border:1px solid #d6d6d6;background:#f7f7f7;font-family:"Open Sans",sans-serif;font-weight:700;font-size:11px;color:var(--navy);text-align:center;line-height:30px;white-space:nowrap;overflow:hidden}

/* footer */
.site-footer{left:0;top:1904px;width:1200px;height:265px;background:var(--green);border-top:2px solid var(--green-dark)}
.footer-heading{position:absolute;top:26px;font-size:19px;color:var(--white);white-space:nowrap}
.quick-links{position:absolute;left:207px;top:62px;list-style:none;font-size:13px;line-height:21.5px;color:var(--white);white-space:nowrap}
.field{position:absolute;left:380px;width:247px;height:23px;background:var(--white);border:1px solid #bbb;border-radius:2px;font-size:10px;font-style:italic;color:#888;padding:4px 7px}
.contact-submit{position:absolute;left:380px;top:228px;width:60px;height:21px;background:var(--navy);color:var(--white);font-size:12px;font-weight:700;text-align:center;line-height:21px;border-radius:2px}
.social{position:absolute;left:676px;top:64px;list-style:none;font-size:11.5px;color:var(--white)}
.social li{display:flex;align-items:center;gap:8px;height:32px;white-space:nowrap}
.social li i{display:block;width:21px;height:21px;background:#b7a58d;border:1px solid #e8dcc8}
.footer-art{position:absolute;left:808px;top:26px}
.copyright{left:0;top:2169px;width:1200px;height:26px;background:var(--navy);color:var(--white);font-size:11px;text-align:center;line-height:26px}
</style>
</head>
<body>

<div class="abs utility-bar">
  <div class="utility-links"><span>Login</span><span>|</span><span>Sign Up</span><span>|</span><span>My Account</span><span>|</span><span>Shopping Cart</span></div>
</div>

<header class="abs site-header">
  <div class="brand-name">AMANI LIVING</div>
  <div class="phone">
    <svg width="26" height="26" viewBox="0 0 26 26"><circle cx="13" cy="13" r="11.5" fill="none" stroke="#222" stroke-width="2"/><path d="M9 7.5c-1 1-1.2 2.6-.2 4.6 1.2 2.4 3 4.2 5.2 5.3 2 1 3.5.8 4.4-.2l-2-2.1-1.6.9c-1.2-.6-2.2-1.6-2.9-2.9l.9-1.6z" fill="#222"/></svg>
    010-555-0143
  </div>
  <div class="search">Search
    <svg width="14" height="14" viewBox="0 0 14 14"><circle cx="5.5" cy="5.5" r="4.3" fill="none" stroke="#222" stroke-width="1.6"/><line x1="8.6" y1="8.6" x2="13" y2="13" stroke="#222" stroke-width="1.8"/></svg>
  </div>
</header>

<nav class="abs main-nav">
  <span class="nav-item active">Shop Now</span>
  <span class="nav-item" style="left:288px">Our Story</span>
  <span class="nav-item" style="left:370px">Blog</span>
  <span class="nav-item" style="left:421px">Custom Design</span>
  <span class="nav-item" style="left:540px">Our Shop</span>
  <span class="nav-item" style="left:619px">Press &amp; Mentions</span>
  <span class="nav-item" style="left:749px">Designer &amp; Architects</span>
  <span class="nav-item" style="left:910px">Video</span>
  <span class="nav-item" style="left:967px">Contact</span>
</nav>

<section class="abs hero">
  <h1 class="hero-title">Lorem ipsum<br>dolor sit</h1>
  <p class="hero-copy">Lorem ipsum dolor sit amet consectetuer adipiscing elit sed diam nonummy nibh euismod tincidunt ut laoreet dolore magna aliquam erat volutpat.</p>
  <div class="buy-button">BUY NOW
    <svg class="go" width="28" height="26" viewBox="0 0 28 26"><ellipse cx="14" cy="13" rx="14" ry="13" fill="#fff"/><path d="M8 9l4 4-4 4M14 9l4 4-4 4" fill="none" stroke="#3a963d" stroke-width="2"/></svg>
  </div>
  <svg class="hero-feature" width="514" height="514" viewBox="0 0 514 514" role="img" aria-label="Featured product photo: beaded wire motorcycle sculpture on black">
    <defs><linearGradient id="heroFill" x1="0" y1="0" x2="0" y2="1"><stop offset="0" stop-color="#2a2a2a"/><stop offset="1" stop-color="#151515"/></linearGradient></defs>
    <rect x="75" y="75" width="364" height="364" rx="22" transform="rotate(45 257 257)" fill="url(#heroFill)"/>
  </svg>
  <div class="hero-price">$ 199.00</div>
</section>

<article class="abs promo" style="left:186px">
  <div class="promo-image" role="img" aria-label="Craft magazine covers" style="background:linear-gradient(160deg,#b9aea4,#8e7466)"></div>
  <div class="promo-text"><strong>Lorem ipsum dolor sit</strong><span>Lorem ipsum dolor sit</span></div>
  <div class="promo-button">BROWSE OUR CATALOG <svg width="20" height="18" viewBox="0 0 20 18"><ellipse cx="10" cy="9" rx="10" ry="9" fill="#fff"/><path d="M5 6l3 3-3 3M10 6l3 3-3 3" fill="none" stroke="#3a963d" stroke-width="1.6"/></svg></div>
</article>
<article class="abs promo" style="left:467px">
  <div class="promo-image" role="img" aria-label="Carved wooden bowls" style="background:linear-gradient(180deg,#c9a488,#a4694a)"></div>
  <div class="promo-text"><strong>Lorem ipsum dolor sit</strong><span>Lorem ipsum dolor sit</span></div>
  <div class="promo-button">SHOP NEW ITEMS <svg width="20" height="18" viewBox="0 0 20 18"><ellipse cx="10" cy="9" rx="10" ry="9" fill="#fff"/><path d="M5 6l3 3-3 3M10 6l3 3-3 3" fill="none" stroke="#3a963d" stroke-width="1.6"/></svg></div>
</article>
<article class="abs promo" style="left:746px">
  <div class="promo-image" role="img" aria-label="Pile of striped colourful cushions" style="background:linear-gradient(160deg,#b5473f,#4b3f8a)"></div>
  <div class="promo-text"><strong>Lorem ipsum dolor sit</strong><span>Lorem ipsum dolor sit</span></div>
  <div class="promo-button">READ MORE <svg width="20" height="18" viewBox="0 0 20 18"><ellipse cx="10" cy="9" rx="10" ry="9" fill="#fff"/><path d="M5 6l3 3-3 3M10 6l3 3-3 3" fill="none" stroke="#3a963d" stroke-width="1.6"/></svg></div>
</article>

<div class="abs soft-divider" style="top:1122px"></div>

<h2 class="abs section-title" style="top:1162px">Featured Product</h2>
<div class="abs rule" style="top:1198px"></div>
<svg class="arrow" style="left:186px;top:1173px" width="12" height="20" viewBox="0 0 12 20"><path d="M10 2L3 10l7 8" fill="none" stroke="#a28a6b" stroke-width="3"/></svg>
<svg class="arrow" style="left:1000px;top:1173px" width="12" height="20" viewBox="0 0 12 20"><path d="M2 2l7 8-7 8" fill="none" stroke="#bbb" stroke-width="2.5"/></svg>

<div class="abs product" style="left:187px">
  <div class="product-image" role="img" aria-label="Colourful fabric bangles and bracelets" style="background:linear-gradient(160deg,#3f7f8c,#9c3a5c)"></div>
  <div class="product-name">Product Name</div>
  <div class="product-desc">Lorem ipsum dolor sit amet<br>consectetuer adipiscing</div>
</div>
<div class="abs product" style="left:397px">
  <div class="product-image" role="img" aria-label="Cushions arranged on a window seat" style="background:linear-gradient(180deg,#d3d5c4,#a98979)"></div>
  <div class="product-name">Product Name</div>
  <div class="product-desc">Lorem ipsum dolor sit amet<br>consectetuer adipiscing</div>
</div>
<div class="abs product" style="left:609px">
  <div class="product-image" role="img" aria-label="Woven lidded baskets" style="background:linear-gradient(180deg,#c69a5e,#5c4530)"></div>
  <div class="product-name">Product Name</div>
  <div class="product-desc">Lorem ipsum dolor sit amet<br>consectetuer adipiscing</div>
</div>
<div class="abs product" style="left:817px">
  <div class="product-image" role="img" aria-label="Tan suede tote bag" style="background:linear-gradient(180deg,#e6d7c0,#a87c45)"></div>
  <div class="product-name">Product Name</div>
  <div class="product-desc">Lorem ipsum dolor sit amet<br>consectetuer adipiscing</div>
</div>

<div class="abs soft-divider" style="top:1513px"></div>

<h2 class="abs section-title" style="top:1539px">Categories</h2>
<div class="abs rule" style="top:1587px"></div>
<svg class="arrow" style="left:187px;top:1675px" width="12" height="20" viewBox="0 0 12 20"><path d="M10 2L3 10l7 8" fill="none" stroke="#bbb" stroke-width="2.5"/></svg>
<svg class="arrow" style="left:1002px;top:1675px" width="12" height="20" viewBox="0 0 12 20"><path d="M2 2l7 8-7 8" fill="none" stroke="#bbb" stroke-width="2.5"/></svg>

<div class="abs category" style="left:231px;top:1619px">Cushions</div>
<div class="abs category" style="left:423px;top:1619px">Bed Sheets</div>
<div class="abs category" style="left:616px;top:1619px">Dinning Chairs</div>
<div class="abs category" style="left:808px;top:1619px">Dinning Tables</div>
<div class="abs category" style="left:231px;top:1668px">Decors</div>
<div class="abs category" style="left:423px;top:1668px">Bangles</div>
<div class="abs category" style="left:616px;top:1668px">String Lights</div>
<div class="abs category" style="left:808px;top:1668px">Watches</div>
<div class="abs category" style="left:319px;top:1717px">Jewelry</div>
<div class="abs category" style="left:511px;top:1717px">Shoes</div>
<div class="abs category" style="left:704px;top:1717px">Kitchen Items</div>

<div class="abs rule" style="top:1783px"></div>

<div class="abs newsletter-strip">
  <span class="strip-label" style="left:16px">Newsletter:</span>
  <div class="email-field">Your Email Address:</div>
  <div class="email-submit">SUBMIT</div>
  <div class="strip-divider"></div>
  <span class="strip-label" style="left:448px">We Accept:</span>
  <div class="pay-method" style="left:578px;width:57px">Paywise</div>
  <div class="pay-method" style="left:644px;width:48px">Vantra</div>
  <div class="pay-method" style="left:700px;width:62px">Vantra Go</div>
  <div class="pay-method" style="left:769px;width:52px">Meridia</div>
</div>

<footer class="abs site-footer">
  <div class="footer-heading" style="left:205px">Quick Links</div>
  <ul class="quick-links">
    <li>Shop Now</li><li>Our Story</li><li>Blog</li><li>Custom Design</li><li>Our Shop</li><li>Press &amp; Mentions</li><li>Designer &amp; Architects</li><li>Video</li><li>Contact</li>
  </ul>

  <div class="footer-heading" style="left:380px">QUICK CONTACT</div>
  <div class="field" style="top:63px">Name</div>
  <div class="field" style="top:93px">Phone</div>
  <div class="field" style="top:122px">Email</div>
  <div class="field" style="top:153px;height:62px">Message</div>
  <div class="contact-submit">Submit</div>

  <div class="footer-heading" style="left:676px">Follow Us On</div>
  <ul class="social">
    <li><i></i>Gatherly</li>
    <li><i></i>Linkwell</li>
    <li><i></i><u>Chirrup</u></li>
    <li><i></i>Pinmark</li>
    <li><i></i>Yonder</li>
  </ul>

  <svg class="footer-art" width="206" height="206" viewBox="0 0 206 206" role="img" aria-label="Decorative geometric diamond pattern in orange, cream and green">
    <defs><linearGradient id="artFill" x1="0" y1="0" x2="1" y2="1"><stop offset="0" stop-color="#f0c27a"/><stop offset="1" stop-color="#e2763a"/></linearGradient></defs>
    <rect x="33" y="33" width="140" height="140" rx="8" transform="rotate(45 103 103)" fill="url(#artFill)"/>
  </svg>
</footer>

<div class="abs copyright">© Copyright 2014. AmaniLiving. All Rights Reserved.</div>

</body>
</html>
```